Brook Refrigeration. Refrigeration and air conditioning specialists.

We need a website to promote our business. We would a modern simple design using the colours from our logo and black. We want it to be fun but proffesional.

Target Market(s)

Commercial

Number of Pages Required

4 page

Requirements
Must have
• Home Page, About Us, Services and Contact Us.
• 24/7 365 days service available.
• Brook Refrigeration's dedicated team specialises in commercial refrigeration and air conditioning equipment.
• Based in Joondalup, we cover Perth Metro and surrounding areas.
Nice to have
• KNOWLEDGE . EXPERIENCE . PASSION in bold.
• Our experienced and highly trained technicians provide extensive knowledge and exceptional skills for your commercial refrigeration and air conditioning requirements.
• Pictures of commercial refrigeration.
Should not have
• No mention of domestic services.

```html
<!DOCTYPE html>
<html lang="en">
<head>
<meta charset="utf-8">
<title>Brook Refrigeration</title>
<link href="https://fonts.googleapis.com/css2?family=Lato:wght@400;700;900&display=swap" rel="stylesheet">
<style>
:root{
  --lime:#9bf55b;
  --lime-deep:#8ee04a;
  --purple:#2d1a58;
  --ink:#333;
  --line:#e6e6e6;
  --white:#fff;
}
*{box-sizing:border-box;margin:0;padding:0}
html,body{width:1200px;height:3203px;overflow:hidden}
body{font-family:'Lato',sans-serif;color:var(--ink);background:var(--white);position:relative}
.abs{position:absolute}

/* header */
.brand{left:75px;top:40px;font-weight:900;font-size:34px;line-height:1.05;color:var(--lime-deep);width:230px}
.follow{left:657px;top:48px;display:flex;align-items:center;gap:12px;font-size:14px;font-weight:700;color:var(--purple)}
.dot-social{width:18px;height:18px;border-radius:50%;background:var(--purple)}
.phone-top{left:858px;top:42px;display:flex;align-items:center;gap:10px;font-size:23px;font-weight:700;color:var(--purple)}
.badge{left:1070px;top:30px;width:56px;height:56px;border-radius:50%;border:4px solid var(--purple)}
.main-nav{top:116px;left:558px;display:flex;align-items:center;font-size:15px;font-weight:700;color:#222;text-transform:uppercase}
.main-nav a{color:inherit;text-decoration:none;padding:10px 0}
.main-nav .nav-home{background:var(--lime);width:84px;text-align:center;margin-right:26px}
.main-nav .nav-about{margin-right:44px}
.main-nav .nav-services{margin-right:44px}
.main-nav .nav-why{margin-right:56px}

/* hero */
.hero{left:0;top:172px;width:1200px;height:560px;background:linear-gradient(180deg,#8d9096 0%,#b7b9bb 35%,#9fa0a1 70%,#6e6c66 100%)}
.hero-text{left:0;top:325px;width:1200px;text-align:center;color:var(--white)}
.hero-text .lead{font-size:30px;font-weight:700}
.hero-text h1{font-size:40px;font-weight:900;line-height:1.1;margin-top:4px;text-transform:uppercase}
.hero-text .tag{font-size:30px;font-weight:900;color:var(--lime);margin-top:6px;letter-spacing:1px}
.btn{display:inline-block;background:var(--lime-deep);color:var(--purple);font-weight:900;font-size:15px;text-decoration:none;text-transform:uppercase}
.hero-btn{left:525px;top:518px;width:150px;text-align:center;padding:14px 0}
.dots{left:563px;top:688px;display:flex;gap:9px}
.dots span{width:11px;height:11px;border-radius:50%;background:var(--white)}
.dots span:first-child{background:var(--lime)}

/* headings */
.box-title{border:2px solid var(--purple);color:var(--purple);font-weight:900;font-size:29px;text-align:center;text-transform:uppercase;padding:10px 0}
.box-title em{font-style:normal;color:var(--lime-deep)}

/* about */
.about-title{left:373px;top:790px;width:453px}
.about-copy{left:95px;top:874px;width:1010px;text-align:center;font-size:22px;line-height:1.35;color:#444}
.about-copy h3{font-size:24px;font-weight:900;color:var(--purple);margin:22px 0 8px}
.divider{left:75px;top:1119px;width:1050px;height:1px;background:var(--line)}

/* services */
.services-title{left:477px;top:1185px;width:245px}
.card{top:1297px;width:331px;height:313px;border:2px solid var(--lime-deep);text-align:center;padding:28px 16px 0}
.card h3{font-size:24px;font-weight:900;color:var(--purple);text-transform:uppercase;margin-bottom:10px}
.card p{font-size:14px;line-height:1.8;color:#444}
.card .icon{position:absolute;left:50%;bottom:-34px;transform:translateX(-50%);background:var(--white);padding:0 14px}

/* why choose us */
.why-band{left:0;top:1720px;width:1200px;height:587px;background:linear-gradient(135deg,#eeeeee 0%,#dcdcdc 45%,#e8e8e8 70%,#d2d2d2 100%)}
.why-title{left:446px;top:1785px;width:307px}
.why-copy{left:110px;top:1874px;width:980px;text-align:center;font-size:17.5px;line-height:1.6;color:#444}
.feature{top:1996px;width:340px;text-align:center}
.feature .f-icon{height:66px;display:flex;justify-content:center;align-items:center}
.feature h3{margin-top:36px;font-size:24px;font-weight:900;color:var(--purple);text-transform:uppercase;line-height:1.15}
.feature p{margin-top:14px;font-size:17px;line-height:1.55;color:#444}

/* contact */
.contact-band{left:0;top:2307px;width:1200px;height:651px;background:var(--lime)}
.contact-title{left:446px;top:2377px;width:307px}
.contact-lead{left:0;top:2462px;width:1200px;text-align:center;font-size:18px;font-weight:900;color:var(--purple);line-height:1.6}
.field{background:var(--white);font-size:14px;color:#555;padding:15px 14px}
.submit{left:525px;top:2845px;width:150px;height:45px;background:var(--purple);color:var(--white);font-weight:900;font-size:15px;text-align:center;line-height:45px}

/* footer */
.foot-brand{left:75px;top:3022px;font-size:28px;font-weight:900;color:var(--lime-deep);line-height:1.05;width:180px}
.copyright{left:75px;top:3108px;font-size:13px;line-height:1.9;color:#444}
.foot-col{top:3012px;font-size:14px;color:var(--purple)}
.foot-col h4{font-size:15px;font-weight:900;text-transform:uppercase;margin-bottom:12px}
.foot-col li{list-style:none;line-height:28px;font-weight:700}
.foot-col .row{display:flex;align-items:center;gap:14px;line-height:28px;font-weight:700}
.foot-social{display:flex;gap:14px;margin-top:8px}
</style>
</head>
<body>

<!-- header -->
<div class="abs brand">BROOK<br><span style="font-size:16px">REFRIGERATION</span></div>
<div class="abs follow">FOLLOW US <span class="dot-social"></span><span class="dot-social"></span></div>
<div class="abs phone-top">
  <svg width="20" height="20" viewBox="0 0 24 24"><path fill="#2d1a58" d="M6.6 10.8a15.5 15.5 0 0 0 6.6 6.6l2.2-2.2a1 1 0 0 1 1-.25 11.4 11.4 0 0 0 3.6.57 1 1 0 0 1 1 1V20a1 1 0 0 1-1 1A17 17 0 0 1 3 4a1 1 0 0 1 1-1h3.5a1 1 0 0 1 1 1c0 1.25.2 2.45.57 3.57a1 1 0 0 1-.25 1z"/></svg>
  1300-555-018
</div>
<div class="abs badge"></div>
<nav class="abs main-nav">
  <a class="nav-home" href="#">Home</a><a class="nav-about" href="#">About</a><a class="nav-services" href="#">Services</a><a class="nav-why" href="#">Why choose us</a><a href="#">Contact</a>
</nav>

<!-- hero -->
<div class="abs hero" role="img" aria-label="Photo of an empty commercial cool room with steel shelving and ceiling evaporator units"></div>
<div class="abs hero-text">
  <p class="lead">Our dedicated team specialises in</p>
  <h1>Commercial refrigeration &amp;<br>air conditioning equipment</h1>
  <p class="tag">KNOWLEDGE . EXPERIENCE . PASSION</p>
</div>
<a class="abs btn hero-btn" href="#">Read more</a>
<div class="abs dots"><span></span><span></span><span></span><span></span></div>

<!-- about -->
<h2 class="abs box-title about-title">About <em>Brook</em> Refrigeration</h2>
<div class="abs about-copy">
  <p>Brook Refrigeration are commercial refrigeration and air conditioning specialists providing a comprehensive service throughout the&nbsp; Perth Metro area - 24 hours / 7 days a week.</p>
  <h3>We are customer focused!</h3>
  <p>Every part of our business has been designed to make your life easier, putting you at the heart of everything we do.</p>
</div>
<div class="abs divider"></div>

<!-- services -->
<h2 class="abs box-title services-title">Our services</h2>
<div class="abs card" style="left:75px">
  <h3>Maintenance</h3>
  <p>Regular maintenance checks on refrigeration and air conditioning equipment can greatly increase their lifespan and properly serviced equipment will also work more&nbsp; efficiently. Saving you time&nbsp; and money.</p>
  <div class="icon"><svg width="60" height="60" viewBox="0 0 60 60"><path d="M14 30h10v22H14zM24 32l10-14c3-4 8-1 6 3l-4 8h12c3 0 4 3 3 5l-4 14c-1 3-3 4-6 4H24z" fill="#9bf55b" stroke="#2d1a58" stroke-width="2.5" stroke-linejoin="round"/><circle cx="44" cy="12" r="7" fill="none" stroke="#2d1a58" stroke-width="3"/></svg></div>
</div>
<div class="abs card" style="left:436px">
  <h3>Repair</h3>
  <p>Brook Refrigeration excels in providing a fast and efficient repair service.&nbsp; We understand failed equipment is critical to your business revenue.&nbsp; Give us a call and we'll get your equipment back working in<br>no time!</p>
  <div class="icon"><svg width="62" height="62" viewBox="0 0 62 62" stroke="#2d1a58" stroke-width="3" stroke-linecap="round" fill="none"><path d="M31 4v54M7.6 17.5l46.8 27M7.6 44.5l46.8-27"/><path d="M25 8l6 6 6-6M25 54l6-6 6 6M8 25l8 3-2 8M54 37l-8-3 2-8M8 37l8-3-2-8M54 25l-8 3 2 8"/></svg></div>
</div>
<div class="abs card" style="left:795px">
  <h3>Installation</h3>
  <p>We offer a 'free of charge' site survey to determine the best system to suit your needs. We will then prepare a no&nbsp; obligation quote to give you a&nbsp; breakdown of ALL the costs involved. After that it's up to you! We're always on hand to give you the best advice and guide you through your needs.</p>
  <div class="icon"><svg width="56" height="66" viewBox="0 0 56 66"><rect x="6" y="4" width="30" height="56" fill="#9bf55b" stroke="#2d1a58" stroke-width="2.5"/><line x1="6" y1="24" x2="36" y2="24" stroke="#2d1a58" stroke-width="2.5"/><circle cx="38" cy="46" r="14" fill="#fff" stroke="#2d1a58" stroke-width="2.5"/><path d="M31 39l14 14M45 39L31 53" stroke="#2d1a58" stroke-width="3" stroke-linecap="round"/></svg></div>
</div>

<!-- why choose us -->
<div class="abs why-band" role="img" aria-label="Faded photo of a technician servicing a commercial air conditioning unit"></div>
<h2 class="abs box-title why-title">Why choose us</h2>
<p class="abs why-copy">With over 20 years experience in every aspect of refrigeration and air conditioning services, you can count on the team here at Brook Refrigeration for exceptional results every time.</p>
<div class="abs feature" style="left:70px">
  <div class="f-icon"><svg width="62" height="62" viewBox="0 0 62 62"><path d="M18 24a13 13 0 0 1 26 0z" fill="#9bf55b" stroke="#2d1a58" stroke-width="2.5"/><rect x="15" y="24" width="32" height="5" fill="#2d1a58"/><path d="M10 58c0-12 9-18 21-18s21 6 21 18z" fill="#9bf55b" stroke="#2d1a58" stroke-width="2.5"/><path d="M27 46l10 10M37 46L27 56" stroke="#2d1a58" stroke-width="2.5"/></svg></div>
  <h3>Fully qualified<br>technicians</h3>
  <p>Our technicians are fully qualified and certified to carry out all services.<br>We only employ the best!</p>
</div>
<div class="abs feature" style="left:430px">
  <div class="f-icon"><svg width="66" height="66" viewBox="0 0 66 66"><circle cx="33" cy="33" r="30" fill="#9bf55b" stroke="#2d1a58" stroke-width="3"/><circle cx="33" cy="33" r="21" fill="#fff" stroke="#2d1a58" stroke-width="2.5"/><path d="M33 19v15h10" stroke="#2d1a58" stroke-width="3" fill="none" stroke-linecap="round"/></svg></div>
  <h3>24/7 365 days service<br>available</h3>
  <p>We never close! From early morning maintenance to emergency breakdowns, we've got you covered.</p>
</div>
<div class="abs feature" style="left:790px">
  <div class="f-icon"><svg width="50" height="66" viewBox="0 0 50 66"><path d="M25 63C12 44 5 33 5 24a20 20 0 0 1 40 0c0 9-7 20-20 39z" fill="#9bf55b" stroke="#2d1a58" stroke-width="3"/><circle cx="25" cy="24" r="8" fill="#fff" stroke="#2d1a58" stroke-width="2.5"/></svg></div>
  <h3>Service based in<br>Joondalup</h3>
  <p>We service Perth Metro and<br>surrounding areas.</p>
</div>

<!-- contact -->
<div class="abs contact-band"></div>
<h2 class="abs box-title contact-title">Contact us</h2>
<p class="abs contact-lead">Contact us on 1300 555 018 for out of hours emergencies<br>Or leave us a message.</p>
<div class="abs field" style="left:227px;top:2545px;width:360px;height:50px">Name</div>
<div class="abs field" style="left:614px;top:2545px;width:360px;height:50px">Phone Name</div>
<div class="abs field" style="left:227px;top:2610px;width:747px;height:50px">Email Address</div>
<div class="abs field" style="left:227px;top:2678px;width:747px;height:132px">Message</div>
<div class="abs submit">SUBMIT</div>

<!-- footer -->
<div class="abs foot-brand">BROOK<br><span style="font-size:13px">REFRIGERATION</span></div>
<p class="abs copyright">Copyright © 2018 Brook Refrigeration Pty Ltd.<br>All Rights Reserved.<br>ABN 12 345 678 901.</p>
<div class="abs foot-col" style="left:414px">
  <h4>Site map</h4>
  <ul><li>Home</li><li>About</li><li>Services</li><li>Why Coose Us</li><li>Contact Us</li></ul>
</div>
<div class="abs foot-col" style="left:628px">
  <h4>Contact us</h4>
  <div class="row"><svg width="14" height="14" viewBox="0 0 24 24"><path fill="#2d1a58" d="M6.6 10.8a15.5 15.5 0 0 0 6.6 6.6l2.2-2.2a1 1 0 0 1 1-.25 11.4 11.4 0 0 0 3.6.57 1 1 0 0 1 1 1V20a1 1 0 0 1-1 1A17 17 0 0 1 3 4a1 1 0 0 1 1-1h3.5a1 1 0 0 1 1 1c0 1.25.2 2.45.57 3.57a1 1 0 0 1-.25 1z"/></svg>1300 555 018</div>
  <div class="row"><svg width="14" height="12" viewBox="0 0 14 12"><rect width="14" height="12" fill="#2d1a58"/><path d="M0 1l7 5 7-5" stroke="#fff" fill="none" stroke-width="1.3"/></svg>info@brookrefrigeration.example</div>
</div>
<div class="abs foot-col" style="left:907px">
  <h4>Follow us</h4>
  <div class="foot-social"><span class="dot-social"></span><span class="dot-social"></span></div>
</div>

</body>
</html>
```